Brochure/flyer for our trip to Paris

Our company is taking us all on a summer trip to Paris. We have some key information that we need to tell everybody about the trip. We think a nicely designed brochure or flyer, which uses our brand colours and guidelines, would be something nice to keep during the trip and as a memento afterwards.

We are looking for a brochure or a flyer which contains all the info in the attached document.

This needs to happen really fast as we actually go to Paris on the 13th August. We also need time to print it!

We can provide a library of icons. All images in the document can be changed. you don't have to use the images in the document.

Target Market(s)

People in our company. They are fun and as this is for a party the flyer needs to feel uplifting.

Industry/Entity Type

Health

Font styles to use
Other font styles liked:
• Nexa - please see attached font.

Requirements
Must have
• Designers must stick to our brand guideline, font and the colours we use.
• Please also see attached content for the flyer.
• This website shows our style - https://www.lorventi.com/fr
Should not have
• Please don't make it too tacky or too much about French things. It can be a bit playful but not too much.

```html
<!DOCTYPE html>
<html lang="en">
<head>
<meta charset="utf-8">
<title>Lorventi Paris 2016 – Trip Brochure</title>
<link rel="stylesheet" href="https://fonts.googleapis.com/css2?family=Questrial&display=swap">
<style>
:root{
  --blue:#1f3ee0;
  --mint:#74f5c2;
  --red:#f7380f;
  --sky:#3f94f5;
  --white:#ffffff;
}
*{margin:0;padding:0;box-sizing:border-box}
html,body{width:778px;height:1200px;overflow:hidden;background:var(--white)}
body{font-family:"Questrial",sans-serif;color:var(--white)}
.brochure{position:relative;width:778px;height:1200px;overflow:hidden;
  background:repeating-linear-gradient(to bottom,
    var(--blue) 0 100px,var(--mint) 100px 200px,var(--red) 200px 300px,var(--sky) 300px 400px)}
.panel{position:absolute;padding:14px 18px 0 18px;font-size:7.6px;line-height:1.25}
.panel h2{font-weight:400;font-size:18px;letter-spacing:.3px;margin:4px 0 12px}
.panel p{margin-bottom:9px}
.panel ul{list-style:none;margin:0 0 10px 0}
.panel li{position:relative;padding-left:24px;margin-bottom:0}
.panel li::before{content:"-";position:absolute;left:0}
.panel .label{margin-bottom:8px}
strong{font-weight:400;text-shadow:0 0 .4px currentColor}

.cover{left:0;top:0;width:260px;height:400px;text-align:center;padding:0}
.cover .brand{position:absolute;left:0;right:0;top:152px;font-size:56px;line-height:1;letter-spacing:-1px}
.cover .sub{position:absolute;left:0;right:0;top:223px;font-size:13px}

.inside-blank{left:260px;top:0;width:236px;height:400px;background:var(--white)}

.travel{left:520px;top:0;width:236px;height:400px;background:var(--blue);padding-top:14px}
.travel h2{margin-bottom:8px}
.hotel-map{display:block;width:156px;height:76px;margin-top:4px}

.metro{left:0;top:400px;width:238px;height:400px;background:var(--mint)}
.translations{left:260px;top:400px;width:236px;height:396px;background:var(--red)}
.translations p{margin-bottom:11px}
.emergency{left:520px;top:400px;width:236px;height:396px;background:var(--sky)}
.emergency p{margin-bottom:11px}

.visits{background:var(--white);color:var(--sky)}
.visits h2{color:var(--blue);font-size:19px}
.visits-map{left:0;top:800px;width:238px;height:400px}
.paris-map{display:block;width:200px;height:156px;margin-top:12px}
.visits-list{left:260px;top:796px;width:240px;height:404px}
.visits-list .place{margin-bottom:12px}
.visits-list .name{color:var(--blue)}
.visits-list .url{word-break:break-all}
</style>
</head>
<body>
<main class="brochure">

  <section class="panel cover">
    <div class="brand">Lorventi</div>
    <div class="sub">Paris 2016</div>
  </section>

  <section class="panel inside-blank"></section>

  <section class="panel travel">
    <h2>Travel Information</h2>
    <p class="label">Outward Journey 13/08/16:</p>
    <ul>
      <li>Meet at Kings Cross St Pancras International Station no later than <strong>6:55am</strong>.</li>
      <li>Our train departs at 7:55am and arrives in Paris at 11:17am local time.</li>
    </ul>
    <p class="label" style="margin-top:18px">Return Journey 14/08/16:</p>
    <ul>
      <li>Meet at Gare Du Nord no later than <strong>2:00 pm</strong>.</li>
      <li>Our train departs at 3:13pm and arrives in London at 4:30pm local time.</li>
    </ul>
    <h2 style="margin-top:20px">Hotel Information</h2>
    <p>HOTEL DES TROIS TILLEULS<br>12, rue Marcelline Vaudé<br>75001<br>Paris<br>France</p>
    <p>Tel: +33 1 40 00 00 17</p>
    <p>Nearest Metro Station: Châtelet&nbsp; (As Pictured)</p>
    <svg class="hotel-map" role="img" aria-label="Street map showing the hotel near Châtelet metro station" viewBox="0 0 156 76">
      <rect width="156" height="76" fill="#e9e6df"/>
    </svg>
  </section>

  <section class="panel metro">
    <h2>Metro Help</h2>
    <p>You have each been given 3 Metro tickets to help you on your way. Although you may need additional tickets depending on what your plans are in your free time.</p>
    <p>They are €4 for a single journey. Once you're in the Metro station, how to use the tickets is pretty self explanatory. Tip from Clarisse, the tickets have a magnetic strip so try and keep them away from bank cards etc. If you find that any of your tickets do not work, you can ask at the kiosk for a replacement.</p>
    <p>The best way to find your way around is to use RouteMapper or alternatively:</p>
    <p>www.citytransit-guide.fr/itineraries/en/search</p>
  </section>

  <section class="panel translations">
    <h2>Translations</h2>
    <p>Some Must-know French Phrases for Savvy Travellers:</p>
    <p>Bonjour. (Hello)</p>
    <p>Oui / Non (Yes / No)</p>
    <p>Parlezvous anglais ? (Do you speak English?)</p>
    <p>Où est le métro? (Where is the Metro?)</p>
    <p>Où est...? (Where is...?)</p>
    <p>Où est le guichet ? (Where is the ticket window?)</p>
    <p>Combien ça coûte? (How much does it cost?)</p>
    <p>Merci! (Thank you!)</p>
    <p>Bonsoir (Hello/good evening)</p>
    <p>Au Revoir (Goodbye)</p>
    <p>Puisje me connecter à Internet? (Can I get on the internet?)</p>
    <p>Je ne comprends pas. (I don't understand)</p>
    <p>Je ne sais pas. (I don't know)</p>
    <p>Estce que vous pouvez l'écrire? (Could you please write it down?)</p>
    <p>Pouvezvous m'aider, s'il vous plaît? (Can you help me please?)</p>
  </section>

  <section class="panel emergency">
    <h2>Emergency</h2>
    <p>Maren 07700900141</p>
    <p>Tobias 07700900262</p>
    <p>Felix 07700900383</p>
    <p>Ines 07700900427</p>
    <p>French Emergency Services 112</p>
    <h2 style="margin-top:18px">Itinerary</h2>
    <p class="label">13th August</p>
    <ul>
      <li>Arrive in Paris at 11:17am local time.</li>
      <li>Drop bags to hotel, grab lunch and enjoy our 1 hour River Seine Tour.</li>
      <li>Free time 2:30-7pm (you will need to go and officially check in at the hotel and get ready for the evening within this time).</li>
      <li>7:00pm Drinks and dinner at...</li>
      <li>Late night drinks at...</li>
    </ul>
    <p class="label">14th August</p>
    <ul>
      <li>Check out between 9:10am at the latest and enjoy some breakfast at the hotel.</li>
      <li>Casual walk up to Gare du nord, enjoying Paris that little bit more before we leave.</li>
      <li>Everyone must be at Gare du nord by 2:00pm at the very latest to check in!</li>
    </ul>
  </section>

  <section class="panel visits visits-map">
    <h2>Book Your Visits</h2>
    <p>If you'd like to see some of the most famous monuments in Paris, we recommend you book your tickets in advance.</p>
    <p>Here are the most touristic places in Paris :</p>
    <svg class="paris-map" role="img" aria-label="Illustrated map of Paris marking the main tourist landmarks" viewBox="0 0 200 156">
      <rect width="200" height="156" fill="#c9b98f"/>
    </svg>
  </section>

  <section class="panel visits visits-list">
    <h2>Book Your Visits</h2>
    <p class="place"><span class="name">"La Tour eiffel"</span><br>(Tube 9 and 6, "Trocadero" station)<br><span class="url">www.tower-visits.fr/en/planning-your-visit/buying-tickets.html</span></p>
    <p class="place"><span class="name">Sacré Coeur</span>: Free Entrance<br>(Tube 2 and 12)<br><span class="url">www.basilica-hill.fr/english/visit-and-audio-guide/article/opening-hours</span></p>
    <p class="place"><span class="name">Le Louvre</span>: We advise you to visit the place from outside only, time is too short for the museum<br><span class="url">www.grand-musee.fr/en/visitor-tips</span></p>
    <p class="place"><span class="name">Notre Dame</span>: Walking Distance or line 4<br>("Cite" station)<br><span class="url">www.cathedral-isle.fr/visit.php?page=314</span></p>
    <p class="place"><span class="name">Musée d'Orsay</span>: Buy ticket online<br>(Line 12)<br><span class="url">www.riverside-museum.fr/en/visit/admission/ticket-purchase.html</span></p>
  </section>

</main>
</body>
</html>
```